Business Card Design Project

We are after a business card design for our construction company. Called N & V Corrabel Home Build Studio. We build designer homes mainly one of's. We would like something with punch, eye catching like the homes we build, modern style maybe geometrical or slightly abstract. It is a long business name we realise but we wont mind if our name is more in the back ground making Construction Solutions the focus ??? Colours maybe purple and black ??? Don't really have any set colours.

Industry/Entity Type

Construction

Requirements
Must have
• Business name contact details and our personal names perhaps at bottom somewhere
Nice to have
• A business card which has a simple easily recognised symbol or logo on it

```html
<!DOCTYPE html>
<html lang="en">
<head>
<meta charset="utf-8">
<title>N &amp; V Corrabel Home Build Studio – Business Card</title>
<link rel="stylesheet" href="https://fonts.googleapis.com/css2?family=Michroma&display=swap">
<style>
  :root {
    --card-teal: #22836f;
    --halftone-purple: #7a2fd1;
    --halftone-violet: #9a3fe0;
    --contact-white: #ffffff;
    --brand-ink: #261640;
  }
  html, body {
    margin: 0;
    padding: 0;
    width: 1200px;
    height: 738px;
    overflow: hidden;
    background: var(--card-teal);
  }
  .card {
    position: relative;
    width: 1200px;
    height: 738px;
    overflow: hidden;
    background: var(--card-teal);
    font-family: "Michroma", sans-serif;
  }
  .halftone-pattern {
    position: absolute;
    inset: 0;
    width: 1200px;
    height: 738px;
  }
  .contact {
    position: absolute;
    left: 30px;
    top: 482px;
    width: 630px;
    text-align: center;
    color: var(--contact-white);
    font-size: 46px;
    line-height: 72px;
    letter-spacing: 3px;
    white-space: nowrap;
  }
  .contact p {
    margin: 0;
  }
  .contact-email {
    letter-spacing: 6px;
  }
  .brand {
    position: absolute;
    left: 680px;
    top: 440px;
    width: 500px;
    text-align: center;
    color: var(--brand-ink);
    font-weight: 400;
    white-space: nowrap;
  }
  .brand-initials {
    display: block;
    font-size: 80px;
    line-height: 96px;
    letter-spacing: 4px;
  }
  .brand-surname {
    display: block;
    font-size: 64px;
    line-height: 84px;
  }
  .brand-tagline {
    display: block;
    margin-top: 12px;
    font-size: 30px;
    line-height: 38px;
    letter-spacing: 1px;
  }
</style>
</head>
<body>
  <main class="card">
    <svg class="halftone-pattern" viewBox="0 0 1200 738" role="img" aria-label="Purple halftone dot pattern radiating in concentric arcs from the top left and bottom right corners">
      <defs>
        <radialGradient id="arc-top-left" cx="440" cy="-110" r="600" gradientUnits="userSpaceOnUse">
          <stop offset="0" stop-color="var(--halftone-purple)" stop-opacity="0.85"/>
          <stop offset="0.45" stop-color="var(--halftone-violet)" stop-opacity="0.75"/>
          <stop offset="0.72" stop-color="var(--halftone-purple)" stop-opacity="0.35"/>
          <stop offset="1" stop-color="var(--halftone-purple)" stop-opacity="0"/>
        </radialGradient>
        <radialGradient id="arc-bottom-right" cx="1240" cy="720" r="330" gradientUnits="userSpaceOnUse">
          <stop offset="0" stop-color="var(--halftone-violet)" stop-opacity="0.85"/>
          <stop offset="0.6" stop-color="var(--halftone-purple)" stop-opacity="0.45"/>
          <stop offset="1" stop-color="var(--halftone-purple)" stop-opacity="0"/>
        </radialGradient>
      </defs>
      <rect width="1200" height="738" fill="url(#arc-top-left)"/>
      <rect width="1200" height="738" fill="url(#arc-bottom-right)"/>
    </svg>

    <section class="contact">
      <p class="contact-name">John Doe</p>
      <p class="contact-phone">0101 010 101</p>
      <p class="contact-email">email@web.xx</p>
    </section>

    <section class="brand">
      <span class="brand-initials">N &amp; V</span>
      <span class="brand-surname">Corrabel</span>
      <span class="brand-tagline">Home Build Studio</span>
    </section>
  </main>
</body>
</html>
```